Namibia currently imports 60% of its food. Harvest Crest Oruva is an initiative which will assist Namibia to become self sustainable in terms of food production. We aim to do this through the development of 3 agricultural production zones which will include farming zones, local farmer assistance, processing and distribution of the final products. Please see our project overview attached.

```html
<!DOCTYPE html>
<html lang="en">
<head>
<meta charset="utf-8">
<title>Harvest Crest Oruva</title>
<link href="https://fonts.googleapis.com/css2?family=Marcellus&family=Lato:wght@400;700;900&display=swap" rel="stylesheet">
<style>
:root{
  --green:#17683a;
  --green-deep:#0f5a2f;
  --ink:#1c1c1c;
  --muted:#444;
  --link-blue:#3a8fc2;
  --paper:#ffffff;
  --footer:#1f201f;
  --line:#e3e3e3;
}
*{box-sizing:border-box;margin:0;padding:0}
html,body{width:1200px;height:4232px;overflow:hidden;background:var(--paper)}
body{position:relative;font-family:'Lato',sans-serif;color:var(--ink)}
.btn{position:absolute;display:flex;align-items:center;justify-content:center;font:700 13px 'Lato',sans-serif;border-radius:4px 14px 4px 4px}
.btn-green{background:var(--green);color:#fff}
.btn-white{background:#fff;color:var(--ink)}

/* hero */
.hero{position:absolute;left:0;top:0;width:1200px;height:623px;background:linear-gradient(100deg,#3b4a3f 0%,#4e6a45 35%,#5c7a3d 60%,#2f4a24 100%)}
.hero-photo{position:absolute;inset:0;background:linear-gradient(180deg,rgba(200,210,215,.35) 0%,rgba(60,90,40,0) 35%,rgba(20,40,15,.35) 100%)}
.nav{position:absolute;left:110px;top:33px;width:978px;height:89px;background:#fff;border-radius:4px}
.brand{position:absolute;left:22px;top:30px;font:400 28px 'Marcellus',serif;color:var(--green);letter-spacing:.5px}
.nav-links{position:absolute;left:323px;top:36px;display:flex;gap:34px;font:700 12.5px 'Lato',sans-serif;color:#222}
.nav-dot{position:absolute;left:332px;top:60px;width:8px;height:8px;border-radius:50%;background:var(--link-blue)}
.hero h3{position:absolute;left:110px;top:230px;font:400 30px 'Marcellus',serif;color:#fff;letter-spacing:2px}
.hero h1{position:absolute;left:110px;top:290px;font:400 72px 'Marcellus',serif;color:#fff;letter-spacing:5px}
.hero .tag{position:absolute;left:110px;top:392px;font:400 21px 'Marcellus',serif;color:#fff;letter-spacing:1.5px}

/* about */
.about-photo{position:absolute;left:110px;top:707px;width:508px;height:513px;background:linear-gradient(180deg,#c9d4dc 0%,#a9b3b6 40%,#5d7a3a 62%,#3a5e26 100%)}
.about-card{position:absolute;left:529px;top:768px;width:556px;height:550px;background:#fff;box-shadow:0 2px 14px rgba(0,0,0,.12)}
.about-card h2{position:absolute;left:53px;top:75px;font:400 40px 'Marcellus',serif;letter-spacing:2px}
.about-card .copy{position:absolute;left:55px;top:150px;width:460px;font:400 14px/33px 'Lato',sans-serif;letter-spacing:1px}
.about-card .copy p+p{margin-top:8px}

/* solution */
.solution{position:absolute;left:0;top:1405px;width:1200px;height:492px}
.solution-green{position:absolute;left:0;top:0;width:660px;height:492px;background:var(--green);border-top-left-radius:110px}
.solution-photo{position:absolute;left:638px;top:0;width:562px;height:492px;background:linear-gradient(160deg,#6f7f7a 0%,#8a6a45 45%,#5a3a20 100%);border-bottom-right-radius:110px}
.solution h2{position:absolute;left:106px;top:60px;font:400 42px 'Marcellus',serif;color:#fff;letter-spacing:2px}
.solution .copy{position:absolute;left:112px;top:138px;width:470px;font:400 12.5px/22px 'Lato',sans-serif;color:#fff;letter-spacing:.3px}
.solution .copy p+p{margin-top:12px}

/* markets */
.section-title{position:absolute;left:0;width:1200px;text-align:center;font:400 42px 'Marcellus',serif;letter-spacing:3px;color:var(--ink)}
.market{position:absolute;top:2078px;width:318px}
.market .ph{height:284px}
.market .num{position:absolute;left:236px;top:248px;width:72px;height:72px;border-radius:50%;background:#fff;box-shadow:0 3px 10px rgba(0,0,0,.15);display:flex;align-items:center;justify-content:center;font:400 24px 'Marcellus',serif;color:#b9a68c;letter-spacing:2px}
.market .name{position:absolute;left:0;top:297px;font:400 22px 'Marcellus',serif;letter-spacing:2px}
.market .region{position:absolute;left:2px;top:330px;font:400 16px 'Marcellus',serif;color:var(--link-blue);letter-spacing:1.5px}

/* sustainability */
.sustain{position:absolute;left:0;top:2527px;width:1200px;height:560px;background:linear-gradient(180deg,#1c6e3d,#236f3f);border-top-left-radius:110px;border-bottom-right-radius:120px;color:#fff}
.sustain h2{position:absolute;left:0;width:1200px;top:50px;text-align:center;font:400 42px 'Marcellus',serif;letter-spacing:3px}
.tab{position:absolute;top:141px;height:41px;border-radius:6px;display:flex;align-items:center;justify-content:center;font:700 13px 'Lato',sans-serif;letter-spacing:.6px}
.tab-on{left:391px;width:207px;background:#fff;color:var(--ink)}
.tab-off{left:608px;width:206px;border:1.5px solid #fff;color:#fff}
.sustain h3{position:absolute;font:400 32px/41px 'Marcellus',serif;letter-spacing:3px}
.sustain .copy{position:absolute;left:117px;top:322px;width:440px;font:400 12.5px/22px 'Lato',sans-serif;letter-spacing:.8px}
.sustain .copy p+p{margin-top:14px}
.yield{position:absolute;top:352px;width:160px;text-align:center;font-family:'Marcellus',serif}
.yield .ic{margin:0 auto;width:56px;height:54px;background:#fff;border-radius:6px;display:flex;align-items:center;justify-content:center}
.yield .lbl{margin-top:12px;font-size:14px;letter-spacing:1.5px}
.yield .amt{margin-top:4px;font-size:18px;letter-spacing:1.5px}
.yield .per{margin-top:3px;font-size:14px;letter-spacing:1.5px}

/* education */
.edu-sub{position:absolute;left:0;width:1200px;top:3224px;text-align:center;font:700 13px 'Lato',sans-serif;color:var(--green);letter-spacing:.6px}
.edu-copy{position:absolute;left:170px;width:860px;top:3270px;text-align:center;font:400 13.5px/28px 'Lato',sans-serif;letter-spacing:.5px}
.course{position:absolute;top:3360px;height:316px;background:#fff;box-shadow:0 2px 12px rgba(0,0,0,.13)}
.course .ph{position:absolute;left:9px;top:13px;right:9px;height:249px}
.course .label{position:absolute;left:15px;top:281px;font:400 16px 'Marcellus',serif;letter-spacing:1.5px}
.course svg{position:absolute;right:16px;top:282px}
.arrow-dot{position:absolute;top:3505px;width:24px;height:24px;border-radius:50%;background:#c9c9c9;display:flex;align-items:center;justify-content:center}

/* footer */
.footer{position:absolute;left:0;top:3768px;width:1200px;height:464px;background:var(--footer);color:#fff}
.footer .mark{position:absolute;left:110px;top:80px;font:400 62px 'Marcellus',serif;color:var(--green);letter-spacing:4px}
.footer .mark-dot{position:absolute;left:82px;top:40px;width:26px;height:26px;border-radius:50%;background:var(--green)}
.newsletter-lbl{position:absolute;left:498px;top:77px;font:400 16px/29px 'Marcellus',serif;letter-spacing:1.5px}
.email{position:absolute;left:623px;top:76px;width:368px;height:46px;background:#fff;color:#333;font:400 13px 'Lato',sans-serif;padding:0 14px;display:flex;align-items:center;letter-spacing:.5px}
.subscribe{position:absolute;left:991px;top:76px;width:92px;height:46px;background:var(--green);display:flex;align-items:center;justify-content:center;font:700 13px 'Lato',sans-serif;letter-spacing:.5px}
.fcol{position:absolute;top:199px}
.fcol h4{font:700 18px 'Lato',sans-serif;letter-spacing:1px;margin-bottom:14px}
.fcol ul{list-style:none;font:400 12.5px/26.5px 'Lato',sans-serif;letter-spacing:.6px}
.contact-row,.social-row{display:flex;align-items:center;gap:14px;font:400 12.5px 'Lato',sans-serif;letter-spacing:.3px;white-space:nowrap}
.contact-row{height:42px}
.social-row{height:40px}
.ico{width:20px;height:20px;border-radius:50%;background:#fff;flex:none;display:flex;align-items:center;justify-content:center}
.footer .rule{position:absolute;left:110px;width:978px;top:427px;height:1px;background:#5a5a5a}
.copyright{position:absolute;left:0;width:1200px;top:440px;text-align:center;font:400 12px 'Lato',sans-serif;letter-spacing:.3px}
</style>
</head>
<body>

<header class="hero">
  <div class="hero-photo" role="img" aria-label="Young farmer checking a tablet in a field of leafy vegetable crops"></div>
  <nav class="nav">
    <div class="brand">HARVEST CREST</div>
    <div class="nav-links"><span>Home</span><span>About Us</span><span>Service</span><span>Project</span><span>Blog</span></div>
    <div class="nav-dot"></div>
    <div class="btn btn-green" style="left:832px;top:23px;width:128px;height:43px">Contact</div>
  </nav>
  <h3>Welcome To</h3>
  <h1>HARVEST CREST</h1>
  <div class="tag">AN ORV AGRI-TECH, FOOD SECURITY INITIATIVE</div>
  <div class="btn btn-white" style="left:110px;top:440px;width:128px;height:40px">Get Started</div>
</header>

<section class="about">
  <div class="about-photo" role="img" aria-label="Grain silos standing behind a field of tall maize"></div>
  <div class="about-card">
    <h2>About Us</h2>
    <div class="copy">
      <p>Namibia is a young democracy in Sub-Saharan Africa with apopulation of approximately 2.5 Million people. The country’s agricultural sector has been slow to keep up with the increasing population.</p>
      <p>As a consequence, approximately 60% of the food required to feed the nation is imported. The elevated cost of these imported foods means a large proportion of the population consume food with low nutritional value.</p>
    </div>
    <div class="btn btn-green" style="left:59px;top:437px;width:129px;height:44px">Contact</div>
  </div>
</section>

<section class="solution">
  <div class="solution-green"></div>
  <div class="solution-photo" role="img" aria-label="Smiling children holding baskets of carrots, onions and potatoes"></div>
  <h2>The “Harvest Crest” Solution</h2>
  <div class="copy">
    <p>The long term intention of the Harvest Crest Oruva program would be to establish 3 distinct food production and processing zones which have access to large amounts of arable land, with high quality soil and strong water resource</p>
    <p>The Harvest Crest Oruva program is currently in the process of securing initial sites in Otavi and Kavango</p>
    <p>The program aims to increase food production in Namibia throughfive distinctive mechanisms in each of the production zones. Ourbelief is that these key mechanisms need be initiatedsimultaneously in order to make a true difference to feed security ina Namibian context.</p>
  </div>
  <div class="btn btn-white" style="left:113px;top:403px;width:128px;height:43px">Read More</div>
</section>

<section class="markets">
  <h2 class="section-title" style="top:1978px">Transport Connections To Relevant Markets</h2>
  <div class="market" style="left:110px">
    <div class="ph" role="img" aria-label="Market stall piled with oranges, bananas and vegetables" style="background:linear-gradient(160deg,#7a3a22,#d98a2a 55%,#5e6a2a)"></div>
    <div class="num">01</div>
    <div class="name">Central Namibia</div>
    <div class="region">Otavi Region</div>
  </div>
  <div class="market" style="left:441px">
    <div class="ph" role="img" aria-label="Farmer in a straw hat harvesting lettuce" style="background:linear-gradient(170deg,#9aa38a,#5d7d45 55%,#3f5f2e);border-radius:60px 60px 0 0"></div>
    <div class="num">02</div>
    <div class="name">North Namibia</div>
    <div class="region">Kavango Region</div>
  </div>
  <div class="market" style="left:771px">
    <div class="ph" role="img" aria-label="Two women in colourful headwraps with fresh peppers and tomatoes" style="background:linear-gradient(160deg,#c78a2a,#b0452c 50%,#5f8a2c);border-radius:0 60px 0 0"></div>
    <div class="num">03</div>
    <div class="name">South Namibia</div>
    <div class="region">Neckartal Dam</div>
  </div>
</section>

<section class="sustain">
  <h2>“Harvest Crest” Sustainability</h2>
  <div class="tab tab-on">Processing Facilities</div>
  <div class="tab tab-off">Sustainable Solutions</div>
  <h3 style="left:113px;top:249px">Processing Facilities</h3>
  <div class="copy">
    <p>Each of the allocated production zones will be furnished with handling, processing and milling facilities for all crops produced as part of the program. These will include Potatoes, Maize and Wheat.</p>
    <p>Harvest Crest Oruva will undertake primary production of the food goods and market them into the Namibian food supply chain.</p>
  </div>
  <h3 style="left:633px;top:246px;width:460px">Anticipated yields per production zone:</h3>
  <div class="yield" style="left:578px">
    <div class="ic"><svg width="32" height="28" viewBox="0 0 32 28"><ellipse cx="11" cy="17" rx="9" ry="8" fill="#d9802a"/><ellipse cx="21" cy="12" rx="9" ry="8" fill="#e8963a"/><ellipse cx="17" cy="20" rx="8" ry="6" fill="#c96e20"/></svg></div>
    <div class="lbl">Potatoes</div><div class="amt">20,000 Ton</div><div class="per">Per Annum</div>
  </div>
  <div class="yield" style="left:760px">
    <div class="ic"><svg width="22" height="34" viewBox="0 0 22 34"><ellipse cx="11" cy="15" rx="6" ry="12" fill="#e7b73a"/><path d="M3 32 C4 20 8 14 11 26 C14 14 18 20 19 32Z" fill="#6c9a3a"/></svg></div>
    <div class="lbl">Maize</div><div class="amt">16,000 Ton</div><div class="per">Per Annum</div>
  </div>
  <div class="yield" style="left:947px">
    <div class="ic"><svg width="24" height="34" viewBox="0 0 24 34"><path d="M12 33 V6" stroke="#b58a3a" stroke-width="2"/><g fill="#d4a24a"><ellipse cx="9" cy="10" rx="3" ry="5"/><ellipse cx="15" cy="10" rx="3" ry="5"/><ellipse cx="9" cy="18" rx="3" ry="5"/><ellipse cx="15" cy="18" rx="3" ry="5"/></g></svg></div>
    <div class="lbl">Wheat</div><div class="amt">6,000 Ton</div><div class="per">Per Annum</div>
  </div>
</section>

<section class="education">
  <h2 class="section-title" style="top:3165px">“Harvest Crest” Education</h2>
  <div class="edu-sub">Give a man a fish and feed him for a day, teach a man to fish and feed him for a lifetime</div>
  <p class="edu-copy">Education is key to empowerment and we embrace that concept. As such, we aim to offer a vocational education scheme for the participants in the Harvest Crest Oruva program. We aim to furnish the participants with the skills to be successful and sustainable farmers in their own rights. Key education outcomes we&nbsp; aim to deliver:</p>
  <div class="arrow-dot" style="left:46px"><svg width="12" height="12" viewBox="0 0 12 12"><path d="M8 2 L3 6 L8 10" stroke="#fff" stroke-width="2" fill="none"/></svg></div>
  <div class="arrow-dot" style="left:1126px"><svg width="12" height="12" viewBox="0 0 12 12"><path d="M4 2 L9 6 L4 10" stroke="#fff" stroke-width="2" fill="none"/></svg></div>
  <div class="course" style="left:117px;width:317px">
    <div class="ph" role="img" aria-label="Farmer carrying a crate of fresh leafy greens in a greenhouse" style="background:linear-gradient(170deg,#b7c2b0,#6e8d55 60%,#3d5a2c)"></div>
    <div class="label">Farm Management</div>
    <svg width="18" height="14" viewBox="0 0 18 14"><path d="M1 7 H16 M11 2 L16 7 L11 12" stroke="#222" stroke-width="1.6" fill="none"/></svg>
  </div>
  <div class="course" style="left:447px;width:314px">
    <div class="ph" role="img" aria-label="Worker picking tea leaves on a green hillside under a cloudy sky" style="background:linear-gradient(180deg,#cfe0ee 0%,#e6eef3 35%,#6f9a3e 55%,#3f6a25 100%)"></div>
    <div class="label">Crop Management</div>
    <svg width="18" height="14" viewBox="0 0 18 14"><path d="M1 7 H16 M11 2 L16 7 L11 12" stroke="#222" stroke-width="1.6" fill="none"/></svg>
  </div>
  <div class="course" style="left:778px;width:314px">
    <div class="ph" role="img" aria-label="Ploughed field with irrigation rows under a blue sky" style="background:linear-gradient(180deg,#6f9fd0 0%,#b9cfe3 40%,#8a7a62 55%,#5a4c3a 100%)"></div>
    <div class="label">Soil Health and Irrigation</div>
    <svg width="18" height="14" viewBox="0 0 18 14"><path d="M1 7 H16 M11 2 L16 7 L11 12" stroke="#222" stroke-width="1.6" fill="none"/></svg>
  </div>
</section>

<footer class="footer">
  <div class="mark-dot"></div>
  <div class="mark">HCO</div>
  <div class="newsletter-lbl">Join Our<br>Newsletter</div>
  <div class="email">Enter Email Address</div>
  <div class="subscribe">Subscribe</div>

  <div class="fcol" style="left:115px"><h4>Quick Links</h4>
    <ul><li>Home</li><li>About Us</li><li>Service</li><li>Project</li><li>Blog</li><li>Contact&nbsp; Us</li></ul></div>
  <div class="fcol" style="left:368px"><h4>Help Links</h4>
    <ul><li>Privacy Policy</li><li>Terms &amp; Conditions</li><li>Disclaimer</li></ul></div>
  <div class="fcol" style="left:600px"><h4>Contact Info</h4>
    <div class="contact-row"><span class="ico"><svg width="10" height="12" viewBox="0 0 10 12"><path d="M5 11 C2 7 1 5.5 1 4 A4 4 0 0 1 9 4 C9 5.5 8 7 5 11Z" fill="#1f201f"/><circle cx="5" cy="4" r="1.4" fill="#fff"/></svg></span>14 Veld Road, Otavi - 90210</div>
    <div class="contact-row"><span class="ico"><svg width="11" height="11" viewBox="0 0 11 11"><path d="M2 1 L4 1 L5 3.5 L3.8 4.5 C4.5 6 5 6.5 6.5 7.2 L7.5 6 L10 7 L10 9 C10 9.6 9.5 10 9 10 C4.5 10 1 6.5 1 2 C1 1.5 1.4 1 2 1Z" fill="#1f201f"/></svg></span>+1 555 010 2040</div>
    <div class="contact-row"><span class="ico"><svg width="11" height="9" viewBox="0 0 11 9"><rect x="0.5" y="0.5" width="10" height="8" fill="#1f201f"/><path d="M0.5 0.5 L5.5 5 L10.5 0.5" stroke="#fff" fill="none"/></svg></span>info@harvestcrestoruva.example</div>
  </div>
  <div class="fcol" style="left:965px"><h4>Follow Us</h4>
    <div class="social-row"><span class="ico"></span>Pagebook</div>
    <div class="social-row"><span class="ico"></span>Chirper</div>
    <div class="social-row"><span class="ico"></span>Snapgram</div>
    <div class="social-row"><span class="ico"></span>Worknet</div>
  </div>
  <div class="rule"></div>
  <div class="copyright">Copyright © 2024&nbsp; Harvest Crest Oruva. All rights reserved.</div>
</footer>

</body>
</html>
```